Reginald's Book Cover

Need a cover design for a book (paperback and eBook)
Book Title: Songs From The Old Trapline
Book Width: 15.24
Book Height: 22.86
Thickness: approximately 200 pages.
Book is a collection of stories drawn from the author's life, and will be in the local history genre in northern British Columbia, Canada from the period 1930 to the present time.
Author: Reginald Hugh Pettigrew
Must include "As told to Wendy Falkner" on front cover, not on the spine.
Author invites designers creativity and asks that the attached photos be incorporated into the front and back covers in tasteful ways as follows:
- Back Cover_Reginald_Marta_Knobby – goes on back cover
- Back Cover_Grizzly - goes on the back cover
- Front Cover_Mountain Flowers - goes on the front cover
- Front Cover_Reginald_in Alpine - goes on the front cover
Other uses of the photos will be considered.
We apologize for the quality of the photos. Please do what you can.
We look forward to your designs.
Thank you for considering.

Target Market(s)

Lovers of local history, jokes, storytelling, back country hiking and mountain climbing. Men and women 30 years and older. Primary target readership are men and women in their 40's, 50's, 60's, and older, who love local history

Font styles to use
Sans Serif

Requirements
Must have
• Back cover copy must clear and easy to read.
Must appeal to outdoor, back country types.
Nice to have
• Like to see a creative incorporation of the photos provided.
Build on or compliment the colours in the photos

```html
<!DOCTYPE html>
<html lang="en">
<head>
<meta charset="utf-8">
<title>Songs From The Old Trapline – Book Cover</title>
<link rel="stylesheet" href="https://fonts.googleapis.com/css2?family=Alfa+Slab+One&family=Kaushan+Script&family=Oswald:wght@300;400;500;600&family=Ultra&display=block">
<style>
  :root {
    --stage: #e9e4da;
    --ink: #15120e;
    --cream: #f1e3b8;
    --white: #fbf8f1;
    --spine: #0c0c0c;
    --back-a: #7f7a48;
    --back-b: #a08a55;
    --back-c: #b9a677;
    --back-d: #8c8250;
    --sky-a: #7f8c92;
    --sky-b: #c9bb93;
    --sky-c: #e6cf95;
    --ridge-a: #a9a285;
    --ridge-b: #ddd3b6;
    --meadow-a: #a99a44;
    --meadow-b: #c49b22;
    --meadow-c: #9c8a2c;
  }
  * { margin: 0; padding: 0; box-sizing: border-box; }
  html, body { width: 1200px; height: 858px; overflow: hidden; background: var(--stage); }

  .cover {
    position: absolute; left: 75px; top: 66px;
    width: 1050px; height: 726px;
    display: flex;
    box-shadow: 0 6px 18px rgba(0,0,0,.28);
  }
  .panel { position: relative; width: 485px; height: 100%; overflow: hidden; }

  .back-photo {
    position: absolute; inset: 0;
    background:
      radial-gradient(ellipse 60% 30% at 70% 45%, rgba(205,185,140,.55), transparent 70%),
      radial-gradient(ellipse 80% 25% at 40% 88%, rgba(215,200,155,.6), transparent 70%),
      linear-gradient(170deg, var(--back-a) 0%, var(--back-b) 35%, var(--back-c) 60%, var(--back-d) 100%);
  }
  .front-photo {
    position: absolute; inset: 0;
    background:
      radial-gradient(ellipse 55% 9% at 62% 50%, var(--ridge-b), transparent 75%),
      linear-gradient(180deg, var(--sky-a) 0%, var(--sky-b) 18%, var(--sky-c) 36%, var(--ridge-a) 42%, var(--ridge-b) 48%, var(--ridge-a) 54%, var(--meadow-a) 60%, var(--meadow-b) 78%, var(--meadow-c) 100%);
  }

  .title-block { position: absolute; left: 0; top: 0; width: 100%; text-align: center; }
  .title-script {
    position: absolute; left: 0; width: 100%; top: 22px;
    font-family: "Kaushan Script", cursive;
    font-size: 50px; line-height: 60px; color: var(--white);
    text-shadow: 2px 2px 0 rgba(0,0,0,.35);
  }
  .title-slab {
    position: absolute; left: 0; width: 100%;
    font-family: "Ultra", "Alfa Slab One", serif; font-weight: 400;
    font-size: 50px; line-height: 60px; color: var(--ink);
    letter-spacing: 1px;
    text-shadow: 2px 2px 0 var(--cream), 3px 3px 0 rgba(0,0,0,.25);
  }
  .slab-1 { top: 100px; }
  .slab-2 { top: 158px; }
  .told-to {
    position: absolute; left: 0; width: 100%; top: 238px;
    font-family: "Oswald", sans-serif; font-weight: 500;
    font-size: 22px; line-height: 30px; letter-spacing: 0.3em; color: var(--white);
    text-shadow: 1px 1px 2px rgba(0,0,0,.3);
  }

  .blurb {
    position: absolute; left: 31px; top: 326px; width: 424px;
    font-family: "Oswald", sans-serif; font-weight: 300;
    font-size: 12.5px; line-height: 19.5px; color: var(--white);
    text-align: justify;
    text-shadow: 0 0 2px rgba(0,0,0,.25);
  }
  .blurb p + p { margin-top: 19.5px; }
  .blurb strong { font-weight: 500; font-size: 14px; }

  .author-front {
    position: absolute; left: 0; top: 655px; width: 100%; text-align: center;
    font-family: "Oswald", sans-serif; font-weight: 600;
    font-size: 30px; line-height: 40px; letter-spacing: 0.06em; color: var(--white);
    text-shadow: 1px 1px 2px rgba(0,0,0,.35);
  }

  .spine { position: relative; width: 80px; height: 100%; background: var(--spine); }
  .spine-rot {
    position: absolute; left: 80px; top: 0;
    width: 726px; height: 80px;
    transform: rotate(90deg); transform-origin: 0 0;
  }
  .spine-author {
    position: absolute; left: 28px; top: 26px;
    font-family: "Oswald", sans-serif; font-weight: 500;
    font-size: 18px; line-height: 28px; letter-spacing: 0.05em; color: var(--white);
    white-space: nowrap;
  }
  .spine-script {
    position: absolute; left: 405px; top: 16px;
    font-family: "Kaushan Script", cursive;
    font-size: 26px; line-height: 40px; color: var(--white); white-space: nowrap;
  }
  .spine-slab {
    position: absolute; left: 580px; top: 14px; width: 130px;
    font-family: "Ultra", "Alfa Slab One", serif; font-weight: 400;
    font-size: 18px; line-height: 24px; color: var(--white); text-align: center;
    text-shadow: 1px 1px 0 #777;
  }
</style>
</head>
<body>
  <main class="cover">
    <section class="panel back">
      <div class="back-photo" role="img" aria-label="Faded photo of a grizzly bear on a snowy alpine slope"></div>
      <div class="title-block">
        <div class="title-script">Songs From The</div>
        <div class="title-slab slab-1">OLD</div>
        <div class="title-slab slab-2">TRAPLINE</div>
        <div class="told-to">AS TOLD TO WENDY FALKNER</div>
      </div>
      <div class="blurb">
        <p><strong>REGINALD PETTIGREW</strong> is a true old-fashioned story teller. He loves nothing better than a good story, and particularly when he is the one telling the story. He was born and raised in the tiny sawmill town of Larchdale, BC and spent 80 years of his life there before relocating to his current home on the banks of the Wolverine River in Fort Kelsey, BC. In addition to writing this book, Reginald spends his time writing songs, singing, telling jokes, and entertaining his many friends with stories of days gone by.</p>
        <p>At the age of 15 he started his career as a flunky in the cookhouse, then moved on to work as a horse logger, sawmill worker, bush foreman, rancher, cat skinner, forest warden, road and bridge builder, and finished his career as salmon hatchery manager.</p>
        <p>Reginald’s love of the mountains is evident throughout the book, as is his love for the majestic grizzly bears who inhabit them. He spent his spare time mountain climbing, fishing, skiing, snowshoeing, and hiking in the woods near his home. This book is an eclectic collection of stories about family, friends, and adventures, all sprinkled with the author’s unique sense of humour.</p>
      </div>
    </section>

    <section class="spine">
      <div class="spine-rot">
        <div class="spine-author">REGINALD HUGH PETTIGREW</div>
        <div class="spine-script">Songs From The</div>
        <div class="spine-slab">OLD<br>TRAPLINE</div>
      </div>
    </section>

    <section class="panel front">
      <div class="front-photo" role="img" aria-label="Alpine meadow of yellow wildflowers below a snow-streaked mountain under a cloudy sky"></div>
      <div class="title-block">
        <div class="title-script">Songs From The</div>
        <div class="title-slab slab-1">OLD</div>
        <div class="title-slab slab-2">TRAPLINE</div>
        <div class="told-to">AS TOLD TO WENDY FALKNER</div>
      </div>
      <div class="author-front">REGINALD HUGH PETTIGREW</div>
    </section>
  </main>
</body>
</html>
```